Local 7K Joint Optical Promotion Flyer

A flyer to give to a customer group promoting two optical New York City offices and enticing members to come in and use their optical benefits. Flyer should promote use of benefits at our offices and bring covered patients in for exams and eyewear. We will offer $25 off in addition to covered benefits on the flyer.

Target Market(s)

Eye exam and eyeglass customers with covered benefits usable at our offices.

Industry/Entity Type

Group

Requirements
Must have
• Our businesses address and contact info, expiration date of March 31, 2017, ability to update the expiration date on my own, ability to change the group name on my own. Also must be able to have a black and white version along with the color version. Our two logos are attached, as well as a blank logo. Also, the previous flyer we were using is attached as the kpbn7k file.
Nice to have
• Visual enticement to come in to our offices and use their coverage

```html
<!DOCTYPE html>
<html lang="en">
<head>
<meta charset="utf-8">
<title>Local 7K Optical Benefit Flyer – Colour and Black &amp; White</title>
<link rel="stylesheet" href="https://fonts.googleapis.com/css2?family=Montserrat:wght@400;700&family=Open+Sans:wght@400;600;700;800&display=swap">
<style>
  :root {
    --stage-light: #e4e4e4;
    --stage-dark: #8d8d8d;
    --paper: #ffffff;
    --ink: #1e1e1e;
    --box: #efefef;
    --coupon: #232323;
    --coupon-top: #2c2c2c;
  }
  .flyer {
    --accent: #4a97d6;
    --accent-band-a: #3b97e6;
    --accent-band-b: #62b0ef;
    --accent-bright: #4fa3ea;
    --headline: #4fa3ea;
    --photo-a: #e9d9d2;
    --photo-b: #f3ebe8;
    --photo-c: #fbf9f9;
  }
  .flyer--mono {
    --accent: #8e8e8e;
    --accent-band-a: #9a9a9a;
    --accent-band-b: #b3b3b3;
    --accent-bright: #a8a8a8;
    --headline: #ffffff;
    --photo-a: #dcdcdc;
    --photo-b: #ececec;
    --photo-c: #f9f9f9;
  }
  * { box-sizing: border-box; margin: 0; padding: 0; }
  html, body { width: 1200px; height: 847px; overflow: hidden; }
  body {
    background: radial-gradient(ellipse at 50% 35%, var(--stage-light) 0%, #c4c4c4 55%, var(--stage-dark) 100%);
    font-family: "Open Sans", sans-serif;
    position: relative;
  }
  .flyer {
    position: absolute;
    top: 113px;
    width: 490px;
    height: 621px;
    background: var(--paper);
    box-shadow: 0 10px 22px rgba(0,0,0,.35);
    overflow: hidden;
  }
  .flyer--colour { left: 110px; }
  .flyer--mono { left: 650px; }

  .flyer__photo {
    position: absolute; left: 0; top: 0; width: 300px; height: 466px;
    background: linear-gradient(90deg, var(--photo-a) 0%, var(--photo-b) 45%, var(--photo-c) 80%, rgba(255,255,255,0) 100%);
  }
  .flyer__group {
    position: absolute; right: 24px; top: 22px; text-align: right;
    font-family: "Montserrat", sans-serif; color: var(--accent);
  }
  .flyer__group-name { font-size: 16px; letter-spacing: .3px; line-height: 1.2; }
  .flyer__group-title { font-size: 38px; font-weight: 700; line-height: 1; letter-spacing: -.3px; }

  .flyer__heading {
    position: absolute; left: 263px; width: 170px; top: 95px; text-align: center;
    font-family: "Montserrat", sans-serif; color: #333;
  }
  .flyer__year { font-size: 35px; line-height: 1; }
  .flyer__benefit { font-size: 17.5px; margin-top: 1px; padding-bottom: 2px; border-bottom: 2px solid var(--accent); position: relative; }
  .flyer__benefit::after {
    content: ""; position: absolute; left: 50%; bottom: -7px; margin-left: -6px;
    border: 6px solid transparent; border-bottom: 0; border-top-color: var(--accent);
  }

  .flyer__entitled {
    position: absolute; left: 230px; top: 172px; width: 240px;
    font-size: 10.4px; line-height: 1.3; color: var(--accent);
  }
  .flyer__perks { position: absolute; left: 230px; top: 203px; width: 215px; list-style: none; }
  .flyer__perks li {
    position: relative; padding-left: 18px; font-size: 7.6px; line-height: 1.3;
    color: var(--ink); margin-bottom: 6px;
  }
  .flyer__perks li svg { position: absolute; left: 0; top: 1px; }

  .office__brand {
    position: absolute; left: 150px; width: 95px; text-align: center;
    font-size: 9px; color: var(--ink); white-space: nowrap;
    border-bottom: 1px solid var(--accent); padding-bottom: 2px;
    display: flex; flex-direction: column; align-items: center;
  }
  .office__mark { width: 22px; height: 22px; border-radius: 50%; background: var(--accent); margin-bottom: 5px; }
  .office__brand--one { top: 293px; }
  .office__brand--two { top: 373px; }

  .office__details {
    position: absolute; left: 258px; width: 201px; background: var(--box);
    border-left: 1.5px solid var(--accent); padding: 6px 0 5px 18px;
    font-size: 7.2px; line-height: 1.2; color: #333;
  }
  .office__details::before {
    content: ""; position: absolute; left: 0; top: 50%; margin-top: -4px;
    border: 4px solid transparent; border-right: 0; border-left-color: var(--accent);
  }
  .office__details--one { top: 282px; height: 72px; }
  .office__details--two { top: 362px; height: 77px; }

  .flyer__band {
    position: absolute; left: 0; top: 466px; width: 100%; height: 41px;
    background: linear-gradient(90deg, var(--accent-band-a), var(--accent-band-b));
    color: #fff; font-weight: 700; font-size: 14.6px; text-align: center; line-height: 41px;
  }
  .flyer__cut { position: absolute; left: 0; top: 506px; width: 100%; height: 6px; background: var(--coupon); }
  .flyer__cut svg { position: absolute; left: 0; top: 0; }

  .coupon {
    position: absolute; left: 0; top: 509px; width: 100%; height: 112px;
    background: linear-gradient(180deg, var(--coupon-top), var(--coupon));
    color: #fff;
  }
  .coupon__amount {
    position: absolute; left: 38px; top: 3px;
    font-weight: 800; font-size: 62px; line-height: 1;
    color: var(--accent-bright); letter-spacing: -3px;
  }
  .coupon__amount sup { font-size: 28px; vertical-align: 26px; letter-spacing: 0; }
  .coupon__off { position: absolute; left: 93px; top: 64px; font-size: 40px; line-height: 1; font-weight: 400; }
  .coupon__divider { position: absolute; left: 192px; top: 28px; width: 1px; height: 62px; background: #bbb; }
  .coupon__divider::after {
    content: ""; position: absolute; left: 1px; top: 27px;
    border: 4px solid transparent; border-right: 0; border-left-color: #bbb;
  }
  .coupon__body { position: absolute; left: 217px; top: 13px; width: 260px; }
  .coupon__headline { font-weight: 700; font-size: 16.5px; color: var(--headline); line-height: 1.1; }
  .coupon__lead { font-weight: 700; font-size: 11.2px; line-height: 1.2; margin-top: 9px; }
  .coupon__note { font-size: 6.6px; line-height: 1.25; margin-top: 7px; color: #ddd; width: 222px; }
  .coupon__expiry { font-size: 6.6px; margin-top: 8px; color: #ddd; }
</style>
</head>
<body>

<article class="flyer flyer--colour">
  <div class="flyer__photo" role="img" aria-label="Portrait of a woman wearing black-framed eyeglasses"></div>
  <header class="flyer__group">
    <p class="flyer__group-name">UFPW Local 7K Members &amp;</p>
    <h1 class="flyer__group-title">Dependents</h1>
  </header>
  <div class="flyer__heading">
    <p class="flyer__year">Your 2016</p>
    <p class="flyer__benefit">Eye Glasses Benefit</p>
  </div>
  <p class="flyer__entitled">What You Are Entitled To At Carver and Lane Eyecare and Hudson Optical at NO COST To You:</p>
  <ul class="flyer__perks">
    <li><svg width="12" height="7" viewBox="0 0 12 7"><path d="M1 1h10l-1 5H2z" fill="var(--accent)"/></svg>A thorough and professional eye examination checking both eye health and vision</li>
    <li><svg width="12" height="7" viewBox="0 0 12 7"><path d="M1 1h10l-1 5H2z" fill="var(--accent)"/></svg>A Wide Selection of frames fully covered by your plan</li>
    <li><svg width="12" height="7" viewBox="0 0 12 7"><path d="M1 1h10l-1 5H2z" fill="var(--accent)"/></svg>Standard eye glass lenses customized to your prescription</li>
  </ul>

  <div class="office__brand office__brand--one"><span class="office__mark"></span>Hudson Optical Group</div>
  <div class="office__details office__details--one">127 West Avenue, 2nd Floor<br>Between 12th &amp; 13th Streets<br>(212) 555-0148<br>www.hudsonopticalgroup.com<br>Business Hours:<br>Monday and Wednesday 9:30am - 6pm<br>Tuesday, Thursday, and Friday 9:30am - 5:30pm</div>

  <div class="office__brand office__brand--two"><span class="office__mark"></span>Carver &amp; Lane Eyecare</div>
  <div class="office__details office__details--two">640 North Avenue<br>Between 40th and 41st Streets<br>(212) 555-0173<br>www.carverlaneeyes.com<br>Business Hours:<br>Monday &amp; Thursday 9am - 7:30pm<br>Tuesday, Wednesday, &amp; Friday 9am - 6pm<br>Saturday 9am - 1pm</div>

  <p class="flyer__band">Call 212-555-0148 or 212-555-0173 for an appointment</p>
  <div class="flyer__cut"><svg width="490" height="6" viewBox="0 0 490 6"><line x1="20" y1="2" x2="490" y2="2" stroke="#fff" stroke-width="1" stroke-dasharray="2 2"/><circle cx="5" cy="2" r="1.6" fill="none" stroke="#fff" stroke-width=".8"/><path d="M7 2l9-2M7 2l9 2" stroke="#fff" stroke-width=".8"/></svg></div>
  <section class="coupon">
    <p class="coupon__amount"><sup>$</sup>25</p>
    <p class="coupon__off">OFF</p>
    <span class="coupon__divider"></span>
    <div class="coupon__body">
      <h2 class="coupon__headline">A Special Offer Just For You!</h2>
      <p class="coupon__lead">This Coupon Entitles You To $25 Off Any Purchase Beyond Covered Allowance.</p>
      <p class="coupon__note">Upon the use of your optical benefits at your next visit at either of our 2 locations.</p>
      <p class="coupon__expiry">Expires 12/31/16.</p>
    </div>
  </section>
</article>

<article class="flyer flyer--mono">
  <div class="flyer__photo" role="img" aria-label="Black and white portrait of a woman wearing black-framed eyeglasses"></div>
  <header class="flyer__group">
    <p class="flyer__group-name">UFPW Local 7K Members &amp;</p>
    <h1 class="flyer__group-title">Dependents</h1>
  </header>
  <div class="flyer__heading">
    <p class="flyer__year">Your 2016</p>
    <p class="flyer__benefit">Eye Glasses Benefit</p>
  </div>
  <p class="flyer__entitled">What You Are Entitled To At Carver and Lane Eyecare and Hudson Optical at NO COST To You:</p>
  <ul class="flyer__perks">
    <li><svg width="12" height="7" viewBox="0 0 12 7"><path d="M1 1h10l-1 5H2z" fill="var(--accent)"/></svg>A thorough and professional eye examination checking both eye health and vision</li>
    <li><svg width="12" height="7" viewBox="0 0 12 7"><path d="M1 1h10l-1 5H2z" fill="var(--accent)"/></svg>A Wide Selection of frames fully covered by your plan</li>
    <li><svg width="12" height="7" viewBox="0 0 12 7"><path d="M1 1h10l-1 5H2z" fill="var(--accent)"/></svg>Standard eye glass lenses customized to your prescription</li>
  </ul>

  <div class="office__brand office__brand--one"><span class="office__mark"></span>Hudson Optical Group</div>
  <div class="office__details office__details--one">127 West Avenue, 2nd Floor<br>Between 12th &amp; 13th Streets<br>(212) 555-0148<br>www.hudsonopticalgroup.com<br>Business Hours:<br>Monday and Wednesday 9:30am - 6pm<br>Tuesday, Thursday, and Friday 9:30am - 5:30pm</div>

  <div class="office__brand office__brand--two"><span class="office__mark"></span>Carver &amp; Lane Eyecare</div>
  <div class="office__details office__details--two">640 North Avenue<br>Between 40th and 41st Streets<br>(212) 555-0173<br>www.carverlaneeyes.com<br>Business Hours:<br>Monday &amp; Thursday 9am - 7:30pm<br>Tuesday, Wednesday, &amp; Friday 9am - 6pm<br>Saturday 9am - 1pm</div>

  <p class="flyer__band">Call 212-555-0148 or 212-555-0173 for an appointment</p>
  <div class="flyer__cut"><svg width="490" height="6" viewBox="0 0 490 6"><line x1="20" y1="2" x2="490" y2="2" stroke="#fff" stroke-width="1" stroke-dasharray="2 2"/><circle cx="5" cy="2" r="1.6" fill="none" stroke="#fff" stroke-width=".8"/><path d="M7 2l9-2M7 2l9 2" stroke="#fff" stroke-width=".8"/></svg></div>
  <section class="coupon">
    <p class="coupon__amount"><sup>$</sup>25</p>
    <p class="coupon__off">OFF</p>
    <span class="coupon__divider"></span>
    <div class="coupon__body">
      <h2 class="coupon__headline">A Special Offer Just For You!</h2>
      <p class="coupon__lead">This Coupon Entitles You To $25 Off Any Purchase Beyond Covered Allowance.</p>
      <p class="coupon__note">Upon the use of your optical benefits at your next visit at either of our 2 locations.</p>
      <p class="coupon__expiry">Expires 12/31/16.</p>
    </div>
  </section>
</article>

</body>
</html>
```